Brookmere Osteopathy flyer

I want a clean clear DL flyer (but also want an A4 poster) promoting a new Osteopathic business in a semi rural area in Tasmania (Australia).
It can have pictures like the examples attached to show people what Osteopathy is (its like Chiropractic and physiotherapy).
I am the sole practioner and am male, so any pictures would be best to be a white male if possible.
I've attached some wording, you can use all, or none of it
I don't have a phone number for the business yet
info@brookmereosteopathy.example
www.brookmereosteopathy.example
Target Market(s)
Australians, from tradies, professionals, babies to retired people
Industry/Entity Type
Health
Look and feel

```html
<!DOCTYPE html>
<html lang="en">
<head>
<meta charset="utf-8">
<title>Brookmere Osteopathy – DL Flyers</title>
<link rel="stylesheet" href="https://fonts.googleapis.com/css2?family=Saira+Condensed:wght@700&family=Quicksand:wght@500;600;700&display=swap">
<style>
  :root {
    --brand-blue: #1688cb;
    --accent-orange: #f59a33;
    --panel-grey: #8f8f8f;
    --watermark-grey: #a9a9a9;
    --ink: #1d1d1d;
    --paper: #ffffff;
    --stage: #eceae6;
  }
  * { box-sizing: border-box; margin: 0; padding: 0; }
  html, body { width: 1160px; height: 1200px; overflow: hidden; }
  body {
    background: var(--stage);
    font-family: "Quicksand", sans-serif;
    position: relative;
  }
  .flyer {
    position: absolute;
    top: 108px;
    width: 462px;
    height: 985px;
    background: var(--paper);
    overflow: hidden;
    box-shadow: 0 2px 10px rgba(0,0,0,.18);
  }
  .flyer--about { left: 93px; }
  .flyer--reasons { left: 607px; }

  .brand-mark {
    position: absolute;
    top: 12px;
    left: 18px;
    width: 114px; height: 114px;
    border-radius: 50%;
    border: 3px solid var(--brand-blue);
  }
  .brand-name {
    position: absolute;
    top: 30px;
    left: 145px;
    font-family: "Saira Condensed", sans-serif;
    font-weight: 700;
    font-size: 31px;
    line-height: 37px;
    color: var(--brand-blue);
    white-space: nowrap;
  }

  .offer-band {
    position: absolute;
    top: 157px;
    height: 181px;
    background: var(--brand-blue);
  }
  .accent-stripe {
    position: absolute;
    top: 347px;
    height: 12px;
    background: var(--accent-orange);
  }
  .flyer--about .offer-band { left: 190px; right: 0; }
  .flyer--about .accent-stripe { left: 240px; right: 0; }
  .flyer--reasons .offer-band { left: 0; width: 270px; }
  .flyer--reasons .accent-stripe { left: 0; width: 220px; }

  .offer-title {
    position: absolute;
    top: 181px;
    width: 166px;
    font-family: "Saira Condensed", sans-serif;
    font-weight: 700;
    color: var(--paper);
    text-align: center;
    line-height: 1;
  }
  .flyer--about .offer-title { right: 14px; }
  .flyer--reasons .offer-title { left: 14px; }
  .offer-title .line-sm { display: block; font-size: 35px; }
  .offer-title .line-lg { display: block; font-size: 58px; margin-top: -1px; }
  .offer-title .line-md { display: block; font-size: 29px; margin-top: -1px; }

  .grey-panel {
    position: absolute;
    left: 0; right: 0;
    background: var(--panel-grey);
  }
  .flyer--about .grey-panel { top: 425px; height: 137px; }
  .flyer--reasons .grey-panel { top: 428px; height: 343px; }

  .hero-photo {
    position: absolute;
    top: 139px;
    width: 294px; height: 294px;
    border-radius: 50%;
    border: 5px solid var(--paper);
    background: radial-gradient(circle at 45% 45%, #e7e3df 0%, #c9cdd3 45%, #5d6b78 100%);
  }
  .flyer--about .hero-photo { left: -17px; }
  .flyer--reasons .hero-photo { left: 193px; }

  .service-area {
    position: absolute;
    top: 370px;
    right: 14px;
    text-align: right;
    font-weight: 700;
    font-size: 14.5px;
    line-height: 21px;
    color: var(--ink);
  }
  .reasons-intro {
    position: absolute;
    top: 374px;
    left: 15px;
    font-weight: 700;
    font-size: 14.5px;
    line-height: 21px;
    color: var(--ink);
  }

  .about-text {
    position: absolute;
    top: 444px;
    left: 18px; right: 20px;
    text-align: right;
    color: var(--paper);
    font-weight: 500;
    font-size: 15px;
    line-height: 24.5px;
  }

  .photo-row {
    position: absolute;
    top: 599px;
    left: 15px;
    display: flex;
    gap: 10px;
  }
  .photo { width: 211px; height: 168px; }
  .photo--infant { background: linear-gradient(160deg, #7f86a6 0%, #4f8fc2 55%, #b7c3d6 100%); }
  .photo--back { background: linear-gradient(135deg, #7d98a6 0%, #c99b7e 55%, #e6cf8a 100%); }

  .reason-list {
    position: absolute;
    top: 452px;
    left: 16px;
    list-style: none;
  }
  .reason-list li {
    display: flex;
    align-items: center;
    height: 31.4px;
    color: var(--paper);
    font-weight: 500;
    font-size: 15.5px;
    white-space: nowrap;
  }
  .reason-list svg { width: 20px; height: 14px; margin-right: 17px; flex: none; }

  .side-title {
    position: absolute;
    left: 378px;
    top: 465px;
    height: 275px;
    writing-mode: vertical-rl;
    transform: rotate(180deg);
    font-family: "Saira Condensed", sans-serif;
    font-weight: 700;
    font-size: 29px;
    line-height: 34px;
    color: var(--watermark-grey);
    white-space: nowrap;
  }

  .cta {
    position: absolute;
    top: 808px;
    left: 0; right: 0;
    text-align: center;
    font-weight: 700;
    font-size: 20px;
    color: var(--ink);
  }
  .phone-box {
    position: absolute;
    top: 847px;
    left: 67px;
    width: 329px; height: 57px;
    background: var(--brand-blue);
    color: var(--paper);
    display: flex;
    align-items: center;
    justify-content: center;
    gap: 10px;
    font-weight: 700;
    font-size: 28px;
    letter-spacing: .5px;
  }
  .phone-box svg { width: 30px; height: 32px; }
  .address {
    position: absolute;
    top: 930px;
    left: 38px;
    display: flex;
    align-items: center;
    gap: 16px;
    font-weight: 700;
    font-size: 21px;
    color: var(--ink);
    white-space: nowrap;
  }
  .address svg { width: 20px; height: 28px; }
</style>
</head>
<body>

<section class="flyer flyer--about">
  <div class="brand-mark"></div>
  <div class="brand-name">BROOKMERE OSTEOPATHY<br>&amp; DRY NEEDLING</div>

  <div class="offer-band"></div>
  <div class="accent-stripe"></div>
  <div class="grey-panel"></div>
  <div class="hero-photo" role="img" aria-label="Osteopath stretching a female patient's shoulder on a treatment table"></div>

  <h2 class="offer-title">
    <span class="line-sm">FREE INTIAL</span>
    <span class="line-lg">PHYSIO</span>
    <span class="line-md">CONSULTATION</span>
  </h2>

  <p class="service-area">Serving Semi Rural<br>Area In Tasmania - Australia</p>

  <p class="about-text">Osteopaths Use A Combination of Joint Manipulation, Targeted Deep Tissue Massage And Stretching To Improve Function, Relieve Pain And Support The Body’s Ability To Heal Itself.</p>

  <div class="photo-row">
    <div class="photo photo--infant" role="img" aria-label="Practitioner's hands gently treating a sleeping newborn baby"></div>
    <div class="photo photo--back" role="img" aria-label="Osteopath applying pressure to a woman's lower back"></div>
  </div>

  <p class="cta">Call and make an appointment today</p>
  <div class="phone-box">
    <svg viewBox="0 0 30 32" fill="none" stroke="#fff" stroke-width="2" stroke-linecap="round" stroke-linejoin="round"><path d="M7 3l4 7-3 3c1 4 4 8 8 10l3-3 7 4-2 5c-1 1-3 2-5 1C11 27 4 19 3 10c-1-2 0-4 1-5z"/><path d="M18 9a6 6 0 0 1 4 4M19 4a11 11 0 0 1 8 8"/></svg>
    <span>555.014.2736</span>
  </div>
  <div class="address">
    <svg viewBox="0 0 20 28"><path d="M10 1a9 9 0 0 1 9 9c0 7-9 17-9 17S1 17 1 10a9 9 0 0 1 9-9z" fill="#f59a33"/><circle cx="10" cy="10" r="4" fill="#fff"/></svg>
    <span>48 Willow Creek Road, Brookmere</span>
  </div>
</section>

<section class="flyer flyer--reasons">
  <div class="brand-mark"></div>
  <div class="brand-name">BROOKMERE OSTEOPATHY<br>&amp; DRY NEEDLING</div>

  <div class="offer-band"></div>
  <div class="accent-stripe"></div>
  <div class="grey-panel"></div>
  <div class="hero-photo" role="img" aria-label="Osteopath stretching a female patient's shoulder on a treatment table"></div>

  <h2 class="offer-title">
    <span class="line-sm">FREE INTIAL</span>
    <span class="line-lg">PHYSIO</span>
    <span class="line-md">CONSULTATION</span>
  </h2>

  <p class="reasons-intro">Common reasons people<br>visit an osteopath:</p>

  <ul class="reason-list">
    <li><svg viewBox="0 0 20 14"><path d="M1 13C2 7 6 5 12 5V1l7 6-7 6V9C7 9 4 10 1 13z" fill="#fff"/></svg>Back / Neck Pain</li>
    <li><svg viewBox="0 0 20 14"><path d="M1 13C2 7 6 5 12 5V1l7 6-7 6V9C7 9 4 10 1 13z" fill="#fff"/></svg>Headaches / Migraines</li>
    <li><svg viewBox="0 0 20 14"><path d="M1 13C2 7 6 5 12 5V1l7 6-7 6V9C7 9 4 10 1 13z" fill="#fff"/></svg>Joint And Muscle Pain</li>
    <li><svg viewBox="0 0 20 14"><path d="M1 13C2 7 6 5 12 5V1l7 6-7 6V9C7 9 4 10 1 13z" fill="#fff"/></svg>Pregnancy-related Discomfort</li>
    <li><svg viewBox="0 0 20 14"><path d="M1 13C2 7 6 5 12 5V1l7 6-7 6V9C7 9 4 10 1 13z" fill="#fff"/></svg>Disc Related Issues</li>
    <li><svg viewBox="0 0 20 14"><path d="M1 13C2 7 6 5 12 5V1l7 6-7 6V9C7 9 4 10 1 13z" fill="#fff"/></svg>Sciatica</li>
    <li><svg viewBox="0 0 20 14"><path d="M1 13C2 7 6 5 12 5V1l7 6-7 6V9C7 9 4 10 1 13z" fill="#fff"/></svg>Plantar Fasciitis</li>
    <li><svg viewBox="0 0 20 14"><path d="M1 13C2 7 6 5 12 5V1l7 6-7 6V9C7 9 4 10 1 13z" fill="#fff"/></svg>Tendonitis / Bursitis</li>
    <li><svg viewBox="0 0 20 14"><path d="M1 13C2 7 6 5 12 5V1l7 6-7 6V9C7 9 4 10 1 13z" fill="#fff"/></svg>Adhesive Capsulitis (Frozen Shoulder)</li>
    <li><svg viewBox="0 0 20 14"><path d="M1 13C2 7 6 5 12 5V1l7 6-7 6V9C7 9 4 10 1 13z" fill="#fff"/></svg>Tennis / Golfers Elbow</li>
  </ul>

  <div class="side-title">BROOKMERE OSTEOPATHY<br>&amp; DRY NEEDLING</div>

  <p class="cta">Call and make an appointment today</p>
  <div class="phone-box">
    <svg viewBox="0 0 30 32" fill="none" stroke="#fff" stroke-width="2" stroke-linecap="round" stroke-linejoin="round"><path d="M7 3l4 7-3 3c1 4 4 8 8 10l3-3 7 4-2 5c-1 1-3 2-5 1C11 27 4 19 3 10c-1-2 0-4 1-5z"/><path d="M18 9a6 6 0 0 1 4 4M19 4a11 11 0 0 1 8 8"/></svg>
    <span>555.014.2736</span>
  </div>
  <div class="address">
    <svg viewBox="0 0 20 28"><path d="M10 1a9 9 0 0 1 9 9c0 7-9 17-9 17S1 17 1 10a9 9 0 0 1 9-9z" fill="#f59a33"/><circle cx="10" cy="10" r="4" fill="#fff"/></svg>
    <span>48 Willow Creek Road, Brookmere</span>
  </div>
</section>

</body>
</html>
```